Marrowind Business Card Design

We are the largest used car company fro JapanJust need a simple business cards to start with

Used Car

Haruto " Ben" Kobayashi
Operations Director
Marrowind Australia Pty.Ltd.
P.O.Box 517 Tarrendale NSW 2091
M: 0488 612 247
P: 1800 374 835
email : haruto.kobayashi@mrwd.co.jp

```html
<!DOCTYPE html>
<html lang="en">
<head>
<meta charset="UTF-8">
<title>Marrowind Business Card</title>
<link rel="stylesheet" href="https://fonts.googleapis.com/css2?family=Open+Sans:wght@400;600;700;800&display=swap">
<style>
  :root {
    --backdrop: #e6e6e6;
    --card: #fbfbfa;
    --ink: #111111;
    --ink-soft: #4a4a4a;
    --muted: #6b6b6b;
    --accent: #c8161d;
    --divider: #8a8a8a;
  }
  * { box-sizing: border-box; margin: 0; padding: 0; }
  html, body {
    width: 1200px; height: 1200px; overflow: hidden;
    background: var(--backdrop);
    font-family: "Open Sans", Arial, sans-serif;
  }
  .canvas {
    width: 1200px; height: 1200px;
    display: flex; align-items: center; justify-content: center;
  }
  .business-card {
    position: relative;
    width: 1000px; height: 556px;
    background: var(--card);
    box-shadow: 0 10px 30px rgba(0,0,0,0.12);
  }
  .brand {
    position: absolute; left: 160px; top: 228px;
    width: 300px;
  }
  .brand-name {
    font-size: 52px; font-weight: 800; letter-spacing: -0.5px;
    line-height: 1; color: var(--ink);
    white-space: nowrap;
  }
  .brand-entity {
    margin-top: 4px;
    font-size: 23px; font-weight: 600; color: var(--ink-soft);
    letter-spacing: 0.2px;
    white-space: nowrap;
  }
  .divider {
    position: absolute; left: 492px; top: 160px;
    width: 2px; height: 236px;
    background: linear-gradient(to bottom, rgba(138,138,138,0), var(--divider) 50%, rgba(138,138,138,0));
  }
  .contact {
    position: absolute; left: 528px; top: 184px;
    color: var(--ink);
  }
  .contact-name {
    font-size: 25px; font-weight: 700; line-height: 1.2;
    white-space: nowrap;
  }
  .contact-title {
    font-size: 19px; font-weight: 400; color: var(--muted);
    margin-bottom: 14px;
  }
  .contact-list { list-style: none; }
  .contact-item {
    display: flex; align-items: flex-start;
    font-size: 21px; line-height: 1.25; margin-bottom: 2px;
    white-space: nowrap;
  }
  .contact-icon {
    width: 16px; height: 16px; margin: 5px 10px 0 0; flex: none;
    fill: var(--accent);
  }
  .contact-address-line { display: block; }
  .contact-address-line.indent { margin-left: -26px; }
</style>
</head>
<body>
<main class="canvas">
  <section class="business-card" aria-label="Marrowind business card">
    <div class="brand">
      <div class="brand-name">Marrowind</div>
      <div class="brand-entity">Australia Pty.Ltd</div>
    </div>

    <div class="divider"></div>

    <div class="contact">
      <div class="contact-name">Haruto "Ben" Kobayashi</div>
      <div class="contact-title">Operations Director</div>
      <ul class="contact-list">
        <li class="contact-item">
          <svg class="contact-icon" viewBox="0 0 18 18" aria-hidden="true">
            <rect x="5" y="1" width="8" height="16" rx="1.5"/>
            <rect x="6.5" y="3" width="5" height="9" fill="#fbfbfa"/>
          </svg>
          <span>0488 - 612 - 247</span>
        </li>
        <li class="contact-item">
          <svg class="contact-icon" viewBox="0 0 18 18" aria-hidden="true">
            <path d="M4 2 L7 2 L8 6 L6 7.5 C7 10 8.5 11.5 10.5 12.5 L12 10.5 L16 11.5 L16 14.5 C16 15.5 15 16 14 16 C8 15.5 2.5 10 2 4 C2 3 3 2 4 2 Z"/>
          </svg>
          <span>1800 - 374 - 835</span>
        </li>
        <li class="contact-item">
          <svg class="contact-icon" viewBox="0 0 18 18" aria-hidden="true">
            <path d="M9 1.5 L17 8.5 L14.5 8.5 L14.5 16 L11 16 L11 11 L7 11 L7 16 L3.5 16 L3.5 8.5 L1 8.5 Z"/>
          </svg>
          <span>
            <span class="contact-address-line">P.O.Box 517 Tarrendale</span>
            <span class="contact-address-line indent">NSW 2091</span>
          </span>
        </li>
      </ul>
    </div>
  </section>
</main>
</body>
</html>
```